Boutique custom software development company needs new business card

Our nearly 20 year old custom software development company would like to better include the fact that we are now providing Bitcoin services. These new services are B2B include education (how to acquire and securely hold Bitcoin) and integrating Bitcoin payments into existing ecommerce sites or other existing systems. Please keep the card clean and simple. Attached is our current design and some other files. vextorial.com

Target Market(s)

businesses owners interested in long term relationship

Industry/Entity Type

Custom software development and Bitcoin

Contact Information for Business Card

Dale Parker, dale@vextorial.com, vextorial.com, (888) 555-VXTRL

Font styles to use
Other font styles liked:
• monospace

Requirements
Must have
• double-sided
Nice to have
• clean and simple
Should not have
• physical address

```html
<!DOCTYPE html>
<html lang="en">
<head>
<meta charset="utf-8">
<title>Vextorial Business Card</title>
<link rel="stylesheet" href="https://fonts.googleapis.com/css2?family=Roboto+Mono:wght@400;700&family=Open+Sans:wght@400&display=swap">
<style>
  :root {
    --backdrop: #e9e6e1;
    --card-white: #ffffff;
    --brand-blue: #3f72b8;
    --brand-blue-light: #5a8bcf;
    --brand-blue-soft: #4c7ec2;
    --accent-orange: #ef7d22;
    --ink: #2b2b2b;
  }
  * { margin: 0; padding: 0; box-sizing: border-box; }
  html, body {
    width: 900px;
    height: 1200px;
    overflow: hidden;
    background: var(--backdrop);
  }
  .canvas {
    position: relative;
    width: 900px;
    height: 1200px;
  }
  .card {
    position: absolute;
    left: 78px;
    width: 744px;
    height: 442px;
    border-radius: 40px;
  }
  .card-front {
    top: 130px;
    background: var(--card-white);
  }
  .card-back {
    top: 638px;
    background: var(--brand-blue);
  }

  /* Front: brand block */
  .brand {
    position: absolute;
    left: 67px;
    top: 190px;
    display: flex;
    align-items: center;
    gap: 14px;
  }
  .brand-square {
    width: 46px;
    height: 46px;
    background: var(--brand-blue);
  }
  .brand-name {
    font-family: "Roboto Mono", monospace;
    font-weight: 700;
    font-size: 30px;
    color: var(--brand-blue);
    letter-spacing: 0.5px;
  }
  .divider {
    position: absolute;
    left: 376px;
    top: 78px;
    width: 2px;
    height: 288px;
    background: var(--accent-orange);
  }

  /* Front: contact details */
  .details {
    position: absolute;
    left: 407px;
    top: 98px;
    font-family: "Roboto Mono", monospace;
    color: var(--ink);
  }
  .person-name {
    font-weight: 700;
    font-size: 29px;
    color: var(--accent-orange);
    line-height: 36px;
    letter-spacing: 0.5px;
  }
  .person-title {
    font-size: 16px;
    line-height: 22px;
    margin-top: 1px;
  }
  .contact-list {
    list-style: none;
    margin-top: 28px;
    font-size: 16px;
  }
  .contact-list li {
    display: flex;
    align-items: center;
    gap: 8px;
    height: 25px;
  }
  .contact-list svg {
    width: 17px;
    height: 17px;
    fill: var(--accent-orange);
  }
  .services {
    list-style: none;
    margin-top: 33px;
    font-size: 16px;
    line-height: 25px;
  }

  /* Back */
  .back-name {
    position: absolute;
    left: 0;
    right: 0;
    top: 98px;
    text-align: center;
    font-family: "Roboto Mono", monospace;
    font-weight: 700;
    font-size: 112px;
    line-height: 140px;
    color: var(--brand-blue-light);
  }
  .back-tagline {
    position: absolute;
    left: 0;
    right: 0;
    top: 268px;
    text-align: center;
    font-family: "Open Sans", sans-serif;
    font-size: 40px;
    letter-spacing: -1px;
    color: var(--brand-blue-soft);
  }
</style>
</head>
<body>
<main class="canvas">
  <section class="card card-front" aria-label="Business card front">
    <div class="brand">
      <div class="brand-square"></div>
      <span class="brand-name">VEXTORIAL</span>
    </div>
    <div class="divider"></div>
    <div class="details">
      <h1 class="person-name">Dale Parker</h1>
      <p class="person-title">Founding Partner</p>
      <ul class="contact-list">
        <li>
          <svg viewBox="0 0 24 24" aria-hidden="true"><path d="M6.6 10.8a15.2 15.2 0 0 0 6.6 6.6l2.2-2.2c.3-.3.7-.4 1-.2 1.1.4 2.3.6 3.6.6.6 0 1 .4 1 1V20c0 .6-.4 1-1 1A17 17 0 0 1 3 4c0-.6.4-1 1-1h3.5c.6 0 1 .4 1 1 0 1.3.2 2.5.6 3.6.1.3 0 .7-.2 1z"/></svg>
          <span>(888) 555-VXTRL</span>
        </li>
        <li>
          <svg viewBox="0 0 24 24" aria-hidden="true"><path d="M3 5h18v2l-9 6-9-6z M3 9l9 6 9-6v10H3z"/></svg>
          <span>dale@vextorial.com</span>
        </li>
        <li>
          <svg viewBox="0 0 24 24" aria-hidden="true"><circle cx="12" cy="12" r="10"/></svg>
          <span>www.vextorial.com</span>
        </li>
      </ul>
      <ul class="services">
        <li>Custom Software Development</li>
        <li>Bitcoin Education &amp; Payments</li>
      </ul>
    </div>
  </section>

  <section class="card card-back" aria-label="Business card back">
    <p class="back-name">VEXTORIAL</p>
    <p class="back-tagline">custom applications &amp; bitcoin</p>
  </section>
</main>
</body>
</html>
```